Business Card Design

New business card design

Target Market(s)

Residential & Commercial Property Managers

Industry/Entity Type

Plumbing Services

Contact Information for Business Card

Name - Rowan Keddle, title - Director, Phone Number - 0431 286 517, email - rowan@tbk-plumbing.com.au, Company ABN - 73 215 904 386,

Font styles to use
Sans Serif

Colors
0054AA
0677BA
7BADD7
CADEEF
E8F1F8

```html
<!DOCTYPE html>
<html lang="en">
<head>
<meta charset="utf-8">
<title>TBK Plumbing Services – Business Card</title>
<link href="https://fonts.googleapis.com/css2?family=Montserrat:wght@300;400;500;700&display=swap" rel="stylesheet">
<style>
  :root {
    --navy: #1e252d;
    --blue: #0677ba;
    --sky: #29a3dd;
    --mist: #e8f1f8;
    --white: #ffffff;
    --ink: #1e252d;
    --backdrop: #d8d8d6;
  }
  * { box-sizing: border-box; margin: 0; padding: 0; }
  html, body {
    width: 1200px; height: 801px; overflow: hidden;
    background: var(--backdrop);
    font-family: "Montserrat", sans-serif;
  }
  .sheet {
    position: relative; width: 1200px; height: 801px;
    display: flex; align-items: center; justify-content: center; gap: 40px;
  }
  .card {
    position: relative; width: 540px; height: 330px; overflow: hidden;
    box-shadow: 0 10px 28px rgba(0,0,0,0.18);
  }

  /* Front: contact side */
  .card--front { background: var(--white); display: flex; }
  .front-band {
    width: 138px; height: 100%; background: var(--navy);
    display: flex; align-items: center; justify-content: center;
  }
  .band-brand {
    writing-mode: vertical-rl; transform: rotate(180deg);
    color: var(--white); font-weight: 300; font-size: 15px;
    letter-spacing: 0.35em; white-space: nowrap;
    display: flex; align-items: center; gap: 12px;
  }
  .band-brand .brand-dot {
    width: 12px; height: 12px; border-radius: 50%; background: var(--sky);
  }
  .front-body { position: relative; flex: 1; padding: 82px 0 0 44px; }
  .front-decor {
    position: absolute; right: -40px; top: 18px;
    width: 250px; height: 250px; border-radius: 50%; background: var(--mist);
  }
  .contact { position: relative; }
  .contact-name { color: var(--sky); font-weight: 700; font-size: 22px; line-height: 1.1; }
  .contact-title { color: var(--ink); font-weight: 400; font-size: 14px; margin-top: 2px; }
  .contact-list { list-style: none; margin-top: 40px; font-size: 14px; color: var(--ink); line-height: 1.6; }
  .contact-list .label { color: var(--sky); }
  .contact-list li { display: flex; align-items: center; gap: 7px; }
  .contact-list svg { width: 13px; height: 13px; fill: var(--sky); flex: none; }

  /* Back: brand side */
  .card--back {
    background: var(--navy);
    display: flex; align-items: center; justify-content: center;
  }
  .back-brand { display: flex; align-items: center; gap: 18px; color: var(--white); }
  .back-brand .brand-dot { width: 22px; height: 22px; border-radius: 50%; background: var(--sky); }
  .back-brand-text { display: flex; flex-direction: column; align-items: flex-start; font-weight: 300; }
  .back-brand-name { font-size: 72px; line-height: 1; letter-spacing: 0.04em; }
  .back-brand-tag { font-size: 13px; letter-spacing: 0.55em; margin-top: 10px; }
</style>
</head>
<body>
<main class="sheet">
  <section class="card card--front" aria-label="Business card front">
    <div class="front-band">
      <div class="band-brand"><span class="brand-dot"></span>tbk plumbing services</div>
    </div>
    <div class="front-body">
      <div class="front-decor" aria-hidden="true"></div>
      <div class="contact">
        <p class="contact-name">Rowan Keddle</p>
        <p class="contact-title">Director</p>
        <ul class="contact-list">
          <li><span><span class="label">Company ABN</span> - 73 215 904 386</span></li>
          <li>
            <svg viewBox="0 0 24 24" aria-hidden="true"><path d="M6.6 10.8a15.1 15.1 0 0 0 6.6 6.6l2.2-2.2a1 1 0 0 1 1-.25 11.4 11.4 0 0 0 3.6.57 1 1 0 0 1 1 1V20a1 1 0 0 1-1 1A17 17 0 0 1 3 4a1 1 0 0 1 1-1h3.5a1 1 0 0 1 1 1c0 1.25.2 2.45.57 3.57a1 1 0 0 1-.25 1z"/></svg>
            <span>0431 286 517</span>
          </li>
          <li>
            <svg viewBox="0 0 24 24" aria-hidden="true"><path d="M2 5h20v14H2z M3.5 6.5 12 13l8.5-6.5" stroke="#fff" stroke-width="1.4"/></svg>
            <span>rowan@tbk-plumbing.com.au</span>
          </li>
        </ul>
      </div>
    </div>
  </section>

  <section class="card card--back" aria-label="Business card back">
    <div class="back-brand">
      <span class="brand-dot"></span>
      <div class="back-brand-text">
        <span class="back-brand-name">tbk</span>
        <span class="back-brand-tag">plumbing services</span>
      </div>
    </div>
  </section>
</main>
</body>
</html>
```